TOP NOTCH CATALOG RE-DESIGN FOR A NATIONAL BRAND

This Project needs to be redesigned with a new look and feel we will use all the same tires and keep the same writing we will only change the model numbers from QZ to VR then the number
please visit www.valmortires.com for feel of site which will direct your imagination

Target Market(s)

Our Target Market is Truck Drivers throughout the USA

Industry/Entity Type

Trucking Company

Font styles to use
Serif

Requirements
Must have
• Yellow and Black this signify our Brand see attached Logo
Nice to have
• Lion since our logo is that shows a strong product
Should not have
• other tires other than what is listed

```html
<!DOCTYPE html>
<html lang="en">
<head>
<meta charset="utf-8">
<title>Valmor Tires – Tyre Pattern</title>
<link href="https://fonts.googleapis.com/css2?family=Roboto+Slab:wght@500;600;700;800&display=swap" rel="stylesheet">
<style>
:root{
  --yellow:#e9b71b;
  --ink:#111111;
  --title:#5e5e5e;
  --paper:#ffffff;
  --tyre-dark:#1a1a1a;
  --tyre-mid:#7a7a7a;
}
*{box-sizing:border-box;margin:0;padding:0}
html,body{width:1200px;height:776px;overflow:hidden;background:var(--paper)}
.spread{position:relative;width:1200px;height:776px;font-family:"Roboto Slab",serif;color:var(--ink)}
.page-title{position:absolute;left:84px;top:70px;font-weight:800;font-size:44px;letter-spacing:.5px;color:var(--title);line-height:1}
.category{position:absolute;left:83px;width:113px;background:var(--yellow);display:flex;align-items:center;justify-content:center;font-weight:600;font-size:11.5px;letter-spacing:.2px}
.pattern-row{position:absolute;left:216px;display:flex}
.pattern{width:56px;display:flex;flex-direction:column}
.tread{height:42px;margin:0 4px 0 2px;border-radius:10px 10px 2px 2px;background:linear-gradient(90deg,var(--tyre-dark) 0%,var(--tyre-mid) 30%,var(--tyre-dark) 55%,var(--tyre-mid) 80%,var(--tyre-dark) 100%)}
.code{height:12px;background:var(--yellow);font-size:8.5px;font-weight:600;line-height:12px;padding-left:4px;white-space:nowrap}
.pattern:nth-child(n+2) .code{padding-left:9px}
.size-table{position:absolute;left:656px;top:167px;width:472px;border-collapse:collapse}
.size-table td{height:18.8px;border-bottom:1px solid var(--yellow);font-size:6.5px;font-weight:500;vertical-align:middle;white-space:nowrap}
.size-table td.size{width:64px;background:var(--yellow);font-size:8.5px;font-weight:600;padding-left:4px;border-bottom:1px solid var(--paper)}
.size-table td.models{padding-left:4px;word-spacing:5px}
.folio{position:absolute;top:709px;height:21px;background:var(--yellow);font-size:7.5px;font-weight:700;line-height:21px}
.folio.left{left:0;width:73px;padding-left:26px}
.folio.right{left:1123px;width:77px;padding-left:28px}
.brand{position:absolute;left:86px;top:709px;display:flex;align-items:center;gap:7px;font-weight:700;font-size:17px;color:var(--yellow);letter-spacing:.3px;line-height:21px}
.brand-dot{width:15px;height:15px;border-radius:50%;background:var(--yellow)}
</style>
</head>
<body>
<div class="spread">
  <h1 class="page-title">TYRE PATTERN</h1>

  <div class="category" style="top:169px;height:62px">ALL POSITION</div>
  <div class="category" style="top:235px;height:62px">STEER</div>
  <div class="category" style="top:301px;height:322px">DRIVE</div>
  <div class="category" style="top:627px;height:63px">TRAILER</div>

  <div class="pattern-row" style="top:172px">
    <div class="pattern"><div class="tread" role="img" aria-label="Tyre tread photo VR901"></div><div class="code">VR901</div></div>
    <div class="pattern"><div class="tread" role="img" aria-label="Tyre tread photo VR902"></div><div class="code">VR902</div></div>
    <div class="pattern"><div class="tread" role="img" aria-label="Tyre tread photo VR906"></div><div class="code">VR906</div></div>
    <div class="pattern"><div class="tread" role="img" aria-label="Tyre tread photo VR967"></div><div class="code">VR967</div></div>
    <div class="pattern"><div class="tread" role="img" aria-label="Tyre tread photo VR968"></div><div class="code">VR968</div></div>
    <div class="pattern"><div class="tread" role="img" aria-label="Tyre tread photo VR900"></div><div class="code">VR900</div></div>
  </div>
  <div class="pattern-row" style="top:239px">
    <div class="pattern"><div class="tread" role="img" aria-label="Tyre tread photo VR962"></div><div class="code">VR962</div></div>
    <div class="pattern"><div class="tread" role="img" aria-label="Tyre tread photo VR965"></div><div class="code">VR965</div></div>
    <div class="pattern"><div class="tread" role="img" aria-label="Tyre tread photo VR988"></div><div class="code">VR988</div></div>
    <div class="pattern"><div class="tread" role="img" aria-label="Tyre tread photo VR936"></div><div class="code">VR936</div></div>
    <div class="pattern"><div class="tread" role="img" aria-label="Tyre tread photo VR920"></div><div class="code">VR920</div></div>
    <div class="pattern"><div class="tread" role="img" aria-label="Tyre tread photo VR961"></div><div class="code">VR961</div></div>
  </div>
  <div class="pattern-row" style="top:305px">
    <div class="pattern"><div class="tread" role="img" aria-label="Tyre tread photo VR789"></div><div class="code">VR789</div></div>
    <div class="pattern"><div class="tread" role="img" aria-label="Tyre tread photo VR908"></div><div class="code">VR908</div></div>
    <div class="pattern"><div class="tread" role="img" aria-label="Tyre tread photo VR909"></div><div class="code">VR909</div></div>
    <div class="pattern"><div class="tread" role="img" aria-label="Tyre tread photo VR928"></div><div class="code">VR928</div></div>
    <div class="pattern"><div class="tread" role="img" aria-label="Tyre tread photo VR929"></div><div class="code">VR929</div></div>
    <div class="pattern"><div class="tread" role="img" aria-label="Tyre tread photo VR937"></div><div class="code">VR937</div></div>
  </div>
  <div class="pattern-row" style="top:368px">
    <div class="pattern"><div class="tread" role="img" aria-label="Tyre tread photo VR907"></div><div class="code">VR907</div></div>
    <div class="pattern"><div class="tread" role="img" aria-label="Tyre tread photo VR930"></div><div class="code">VR930</div></div>
    <div class="pattern"><div class="tread" role="img" aria-label="Tyre tread photo VR950"></div><div class="code">VR950</div></div>
    <div class="pattern"><div class="tread" role="img" aria-label="Tyre tread photo VR970"></div><div class="code">VR970</div></div>
    <div class="pattern"><div class="tread" role="img" aria-label="Tyre tread photo VR990"></div><div class="code">VR990</div></div>
    <div class="pattern"><div class="tread" role="img" aria-label="Tyre tread photo VR926"></div><div class="code">VR926</div></div>
  </div>
  <div class="pattern-row" style="top:432px">
    <div class="pattern"><div class="tread" role="img" aria-label="Tyre tread photo VR938"></div><div class="code">VR938</div></div>
    <div class="pattern"><div class="tread" role="img" aria-label="Tyre tread photo VR958"></div><div class="code">VR958</div></div>
    <div class="pattern"><div class="tread" role="img" aria-label="Tyre tread photo VR959"></div><div class="code">VR959</div></div>
    <div class="pattern"><div class="tread" role="img" aria-label="Tyre tread photo VR960"></div><div class="code">VR960</div></div>
    <div class="pattern"><div class="tread" role="img" aria-label="Tyre tread photo VR966"></div><div class="code">VR966</div></div>
    <div class="pattern"><div class="tread" role="img" aria-label="Tyre tread photo VR969"></div><div class="code">VR969</div></div>
  </div>
  <div class="pattern-row" style="top:496px">
    <div class="pattern"><div class="tread" role="img" aria-label="Tyre tread photo VR975"></div><div class="code">VR975</div></div>
    <div class="pattern"><div class="tread" role="img" aria-label="Tyre tread photo VR977"></div><div class="code">VR977</div></div>
    <div class="pattern"><div class="tread" role="img" aria-label="Tyre tread photo VR978"></div><div class="code">VR978</div></div>
    <div class="pattern"><div class="tread" role="img" aria-label="Tyre tread photo VR979"></div><div class="code">VR979</div></div>
    <div class="pattern"><div class="tread" role="img" aria-label="Tyre tread photo VR980"></div><div class="code">VR980</div></div>
    <div class="pattern"><div class="tread" role="img" aria-label="Tyre tread photo VR998"></div><div class="code">VR998</div></div>
  </div>
  <div class="pattern-row" style="top:560px">
    <div class="pattern"><div class="tread" role="img" aria-label="Tyre tread photo VR086"></div><div class="code">VR086</div></div>
    <div class="pattern"><div class="tread" role="img" aria-label="Tyre tread photo VR088"></div><div class="code">VR088</div></div>
    <div class="pattern"><div class="tread" role="img" aria-label="Tyre tread photo VR925"></div><div class="code">VR925</div></div>
  </div>
  <div class="pattern-row" style="top:630px">
    <div class="pattern"><div class="tread" role="img" aria-label="Tyre tread photo VR963"></div><div class="code">VR963</div></div>
    <div class="pattern"><div class="tread" role="img" aria-label="Tyre tread photo KD863T"></div><div class="code">KD863T</div></div>
    <div class="pattern"><div class="tread" role="img" aria-label="Tyre tread photo KD876T"></div><div class="code">KD876T</div></div>
  </div>

  <table class="size-table">
    <tr><td class="size">6.50R16</td><td class="models">VR908 VR901</td></tr>
    <tr><td class="size">7.00R16</td><td class="models">VR902 VR928 VR908</td></tr>
    <tr><td class="size">7.50R16</td><td class="models">VR902 VR908 VR928 VR908 VR900</td></tr>
    <tr><td class="size">8.25R16</td><td class="models">VR902 VR908 VR909 VR928 VR958</td></tr>
    <tr><td class="size">8.25R20</td><td class="models">VR902 VR908 VR900 VR909</td></tr>
    <tr><td class="size">9.00R20</td><td class="models">VR902 VR958 VR998</td></tr>
    <tr><td class="size">10.00R20</td><td class="models">VR789 VR902 VR958 VR998</td></tr>
    <tr><td class="size">11.00R20</td><td class="models">VR902 VR908 VR909 VR928 VR936 VR958 VR978 VR979 VR988 VR987 VR950 VR901 VR968 VR998 VR925</td></tr>
    <tr><td class="size">12.00R20</td><td class="models">VR901 VR902 VR00S VR909 VR928 VR958 VR950 VR987 VR998 VR925</td></tr>
    <tr><td class="size">12.00R24</td><td class="models">VR086 VR088 VR902 VR908</td></tr>
    <tr><td class="size">215/75R17.5</td><td class="models">VR961 VR967</td></tr>
    <tr><td class="size">225/70R19.5</td><td class="models">VR967</td></tr>
    <tr><td class="size">235/75R17.5</td><td class="models">VR967</td></tr>
    <tr><td class="size">245/70R19.5</td><td class="models">VR967</td></tr>
    <tr><td class="size">255/70R22.5</td><td class="models">VR967</td></tr>
    <tr><td class="size">265/70R19.5</td><td class="models">VR967</td></tr>
    <tr><td class="size">275/70R22.5</td><td class="models">VR926 VR967</td></tr>
    <tr><td class="size">295/80R22.5</td><td class="models">VR789 VR908 VR959 VR962 VR966 VR975 VR902</td></tr>
    <tr><td class="size">315/80R22.5</td><td class="models">VR902 VR928 VR929 VR959 VR962 VR966</td></tr>
    <tr><td class="size">11R22.5</td><td class="models">VR902 VR928 VR959 VR960 VR961 VR963 VR965 VR967 VR969 VR978 KD863T KD876T VR977 VR926</td></tr>
    <tr><td class="size">11R24.5</td><td class="models">VR902 VR965 VR969 KD863T VR960</td></tr>
    <tr><td class="size">285/75R24.5</td><td class="models">VR965 VR969 KD863T</td></tr>
    <tr><td class="size">295/75R22.5</td><td class="models">VR965 VR969 KD863T KD876T VRS68</td></tr>
    <tr><td class="size">12R22.5</td><td class="models">VR902 VR937 VR938 VR962 VR963 VR965 VR966 VR978 VR980 VR990 VR920</td></tr>
    <tr><td class="size"></td><td class="models">VR938 VR978 VR925 VR968 VR988</td></tr>
    <tr><td class="size">385/65R22.5</td><td class="models">VR906</td></tr>
    <tr><td class="size">205/85R16LT</td><td class="models">VR902 VR928</td></tr>
    <tr><td class="size">235/85R16LT</td><td class="models">VR959z</td></tr>
  </table>

  <div class="folio left">Page 8</div>
  <div class="brand"><span class="brand-dot"></span>VALMOR TIRES</div>
  <div class="folio right">Page 9</div>
</div>
</body>
</html>
```